Business card for a Exhibition booth fabrication company

Hi. My company would like to change our corporate name card. We are an events and Exhibition stand builder company. We would like our corporate name card to resonate what we do. I need someone to create something unique that relates to the industry that I am in. The graphic designer should be creative to incorporate the elements of my industry and try to blend in well in the design of the card. Our aim is to ensure that we are unique and our card can look different from our competitors.
Updates

Target Market(s)

Marketing and events manager from all companies

Contact Information for Business Card

The business card should have the following details:
Name
Job Title
Email
Website

Colors

Designer to choose colors to be used in the design.

Requirements
Must have
• The card must be look something that is relevant to the service that I am providing. My website is: www.velmora-buildworks.com
• You can see my website to get more information on what service that I am doing
Nice to have
• On the back of my card, I would like to have a globe image with the incorporation of my company logo. This is to indicate that my services can be done in any part of the world.

```html
<!DOCTYPE html>
<html lang="en">
<head>
<meta charset="utf-8">
<title>Velmora Buildworks – Business Card</title>
<link rel="stylesheet" href="https://fonts.googleapis.com/css2?family=Arimo:wght@400;700&family=Open+Sans:wght@400;600&display=swap">
<style>
  :root {
    --red: #ed1c24;
    --red-deep: #d71f26;
    --grey-band: #656567;
    --ink: #58595b;
    --ink-soft: #6d6e70;
    --white: #ffffff;
    --stage-light: #dcdddf;
    --stage-dark: #a7a8ab;
    --map-tint: rgba(255, 255, 255, 0.16);
    --logo-silver: #d8d8da;
  }
  * { margin: 0; padding: 0; box-sizing: border-box; }
  html, body { width: 1200px; height: 1119px; overflow: hidden; }
  body {
    position: relative;
    background: linear-gradient(90deg, var(--stage-light) 0%, #c4c5c8 50%, var(--stage-dark) 100%);
    font-family: "Open Sans", Arial, sans-serif;
  }
  .card {
    position: absolute;
    left: 223px;
    width: 755px;
    height: 431px;
    border-radius: 34px;
    overflow: hidden;
  }
  /* Front */
  .card--front { top: 81px; background: var(--white); }
  .front__accent {
    position: absolute; left: 0; top: 59px; width: 15px; height: 48px;
    background: var(--red-deep);
  }
  .front__name {
    position: absolute; left: 28px; top: 56px;
    font-family: "Arimo", Arial, sans-serif; font-weight: 700;
    font-size: 26px; color: var(--red); letter-spacing: 0.2px;
  }
  .front__title {
    position: absolute; left: 28px; top: 92px;
    font-family: "Arimo", Arial, sans-serif; font-size: 19.5px;
    color: var(--ink-soft); letter-spacing: 0.6px;
  }
  .brand {
    position: absolute; left: 370px; top: 70px; width: 360px; height: 110px;
    display: flex; align-items: center; justify-content: center; gap: 14px;
  }
  .brand__dot { width: 26px; height: 26px; border-radius: 50%; background: var(--red); flex: none; }
  .brand__name {
    font-family: "Open Sans", Arial, sans-serif; font-weight: 600;
    font-size: 22px; letter-spacing: 2px; color: var(--ink); text-transform: uppercase;
  }
  .front__address {
    position: absolute; left: 28px; top: 218px;
    font-size: 18px; line-height: 26px; color: var(--ink);
  }
  .contact {
    position: absolute; left: 28px; display: flex; align-items: center; gap: 12px;
    font-size: 18px; color: var(--ink);
  }
  .contact--phone { top: 287px; }
  .contact--email { top: 321px; }
  .contact svg { width: 19px; height: 19px; flex: none; }
  .front__band { position: absolute; left: 0; top: 373px; width: 755px; height: 58px; }
  .front__web {
    position: absolute; left: 28px; top: 378px;
    font-size: 18px; letter-spacing: 1.4px; color: var(--white);
  }
  /* Back */
  .card--back { top: 579px; background: var(--red); }
  .back__map {
    position: absolute; left: 7px; top: 61px; width: 745px; height: 301px;
    background: radial-gradient(ellipse at center, var(--map-tint) 0%, rgba(255,255,255,0.08) 60%, rgba(255,255,255,0) 100%);
  }
  .back__brand {
    position: absolute; left: 0; top: 200px; width: 755px;
    display: flex; align-items: center; justify-content: center; gap: 16px;
  }
  .back__brand .brand__dot { width: 34px; height: 34px; background: var(--logo-silver); }
  .back__brand .brand__name { font-size: 30px; letter-spacing: 4px; color: var(--logo-silver); }
  .back__web {
    position: absolute; left: 0; top: 392px; width: 755px; text-align: center;
    font-size: 20px; letter-spacing: 4px; color: var(--white);
  }
</style>
</head>
<body>

  <section class="card card--front" aria-label="Business card front">
    <div class="front__accent"></div>
    <div class="front__name">DANIEL HARROW</div>
    <div class="front__title">PRESIDENT</div>

    <div class="brand">
      <span class="brand__dot"></span>
      <span class="brand__name">Velmora Buildworks</span>
    </div>

    <div class="front__address">Street Name, City Name<br>Zipcode - 01234</div>

    <div class="contact contact--phone">
      <svg viewBox="0 0 24 24" aria-hidden="true"><path fill="#ed1c24" d="M6.6 10.8c1.4 2.8 3.8 5.1 6.6 6.6l2.2-2.2c.3-.3.7-.4 1-.2 1.1.4 2.3.6 3.6.6.6 0 1 .4 1 1V20c0 .6-.4 1-1 1C10.6 21 3 13.4 3 4c0-.6.4-1 1-1h3.5c.6 0 1 .4 1 1 0 1.2.2 2.4.6 3.6.1.3 0 .7-.2 1z"/></svg>
      <span>012-345-6789</span>
    </div>
    <div class="contact contact--email">
      <svg viewBox="0 0 24 24" aria-hidden="true"><rect x="2" y="5" width="20" height="14" fill="#ed1c24"/><path d="M2 5l10 8 10-8M2 19l7.5-7M22 19l-7.5-7" fill="none" stroke="#fff" stroke-width="1.6"/></svg>
      <span>info@velmora-buildworks.com</span>
    </div>

    <svg class="front__band" viewBox="0 0 755 58" preserveAspectRatio="none" aria-hidden="true">
      <rect x="0" y="0" width="755" height="58" fill="#656567"/>
      <path d="M0 0 H508 C495 10 490 26 470 33 H0 Z" fill="#d71f26"/>
    </svg>
    <div class="front__web">www.velmora-buildworks.com</div>
  </section>

  <section class="card card--back" aria-label="Business card back">
    <div class="back__map" role="img" aria-label="Faint world map spanning the card, indicating worldwide service"></div>
    <div class="back__brand">
      <span class="brand__dot"></span>
      <span class="brand__name">Velmora Buildworks</span>
    </div>
    <div class="back__web">www.velmora-buildworks.com</div>
  </section>

</body>
</html>
```